Maris Dovey Studio Business Cards

Hi - using the information and logo provided I require a two sided business card designed with the following information. The business card is a 'mini card' 3.5" x 1.25".

Front of card should be the logo attached but inverted (so the background is the peach colour and the logo white).

Back should have these details. If we can't fit the Pictogrum and Friendwall part can we just put the little logos.

Tessa Varnold

Art and Design Consultant
Dealer - Curator - Events - Styling - Creative Sourcing

P: 0438 217 604
E: tessa@marisdoveystudio.example
W: www.marisdoveystudio.example
I (pictogram image please): marisdoveystudio F (Friendwall image please): MarisDoveyAdviser

Target Market(s)

Galleries, artists, art buyers, interior design clients, event managers, creative types

Industry/Entity Type

Business

```html
<!DOCTYPE html>
<html lang="en">
<head>
<meta charset="utf-8">
<title>Maris Dovey Studio – Business Cards</title>
<link rel="stylesheet" href="https://fonts.googleapis.com/css2?family=Tinos&display=swap">
<style>
  :root {
    --stage: #5f544e;
    --card-dark: #151515;
    --card-light: #ffffff;
    --peach: #f2b99c;
    --peach-text: #f4c2a6;
    --rule-dark: #3c3c3c;
    --rule-light: #d6d6d6;
    --ink: #1d1d1d;
    --ink-soft: #555555;
    --serif: "Tinos", "Times New Roman", serif;
  }
  * { box-sizing: border-box; margin: 0; padding: 0; }
  html, body {
    width: 1200px; height: 960px; overflow: hidden;
    background: var(--stage);
    font-family: var(--serif);
  }
  .stage { position: relative; width: 1200px; height: 960px; }

  .card { position: absolute; width: 876px; height: 314px; }
  .rule { position: absolute; height: 1px; }

  /* Front */
  .card--front { left: 46px; top: 58px; background: var(--card-dark); }
  .card--front .rule { background: var(--rule-dark); }
  .brand-panel {
    position: absolute; left: 38px; top: 0; width: 318px; height: 216px;
    background: var(--card-light);
    border-radius: 0 0 22px 22px;
  }
  .brand-panel__mark {
    position: absolute; left: 107px; top: 16px; width: 104px; height: 104px;
    border-radius: 50%; background: var(--peach);
  }
  .brand-name {
    position: absolute; left: 0; width: 100%; text-align: center;
    color: var(--peach); font-size: 20px; letter-spacing: 3px;
    text-transform: uppercase; font-family: var(--serif);
  }
  .brand-panel .brand-name { top: 148px; }
  .holder {
    position: absolute; left: 397px; top: 48px; color: var(--peach-text);
  }
  .holder__name { font-size: 38px; line-height: 1.1; letter-spacing: 0.5px; }
  .holder__title { font-size: 22px; margin-top: 2px; }
  .services {
    position: absolute; left: 0; top: 248px; width: 100%;
    text-align: center; color: var(--peach-text); font-size: 25px;
  }

  /* Back */
  .card--back { left: 274px; top: 473px; background: var(--card-light); }
  .card--back .rule { background: var(--rule-light); }
  .back-mark {
    position: absolute; left: 68px; top: 62px; width: 132px; height: 132px;
    border-radius: 50%; background: var(--peach);
  }
  .card--back .brand-name {
    left: 34px; width: 200px; top: 210px; font-size: 15px; letter-spacing: 2px;
  }
  .contact {
    position: absolute; left: 316px; top: 70px;
    color: var(--ink); font-size: 21px; line-height: 34px;
  }
  .social {
    position: absolute; left: 316px; height: 48px;
    display: flex; align-items: center; gap: 12px; color: var(--ink);
  }
  .social__square { width: 30px; height: 30px; background: var(--ink-soft); }
  .social__network {
    font-size: 14px; letter-spacing: 1.5px; text-transform: uppercase;
    color: var(--ink-soft); width: 100px;
  }
  .social__handle { font-size: 25px; }
</style>
</head>
<body>
<main class="stage">

  <section class="card card--front" aria-label="Front of business card">
    <div class="rule" style="left:372px; top:11px; width:442px;"></div>
    <div class="rule" style="left:372px; top:164px; width:442px;"></div>
    <div class="rule" style="left:31px; top:244px; width:783px;"></div>
    <div class="rule" style="left:31px; top:286px; width:783px;"></div>

    <div class="brand-panel">
      <div class="brand-panel__mark"></div>
      <p class="brand-name">Maris Dovey Studio</p>
    </div>

    <div class="holder">
      <h1 class="holder__name">Tessa Varnold</h1>
      <p class="holder__title">(Art and Design Consultant)</p>
    </div>

    <p class="services">Dealer | Curator | Events | Styling | Creative Sourcing</p>
  </section>

  <section class="card card--back" aria-label="Back of business card">
    <div class="rule" style="left:33px; top:35px; width:823px;"></div>
    <div class="rule" style="left:256px; top:185px; width:596px;"></div>
    <div class="rule" style="left:256px; top:233px; width:596px;"></div>
    <div class="rule" style="left:31px; top:285px; width:821px;"></div>

    <div class="back-mark"></div>
    <p class="brand-name">Maris Dovey Studio</p>

    <div class="contact">
      <p>P: 0438 217 604</p>
      <p>E: tessa@marisdoveystudio.example</p>
      <p>W: www.marisdoveystudio.example</p>
    </div>

    <div class="social" style="top:186px;">
      <span class="social__square"></span>
      <span class="social__network">Pictogrum</span>
      <span class="social__handle">MarisDoveyAdviser</span>
    </div>
    <div class="social" style="top:236px;">
      <span class="social__square"></span>
      <span class="social__network">Friendwall</span>
      <span class="social__handle">marisdoveystudio</span>
    </div>
  </section>

</main>
</body>
</html>
```